BOLD & MINIMALIST DESIGN NEEDED

We want a very bold but minimalistic business card design that is impactful and utilizes both sides of the business card. Our current logo is included for your use.

We want bold fonts and good use of negative space. We don't want the logo to overpower the design.

Target Market(s)

Professionals who are building new commercial buildings.

Industry/Entity Type

Construction

Contact Information for Business Card

Name, Title, email, office phone, cell phone, website

Font styles to use
Serif
Sans Serif

Requirements
Must have
• Bold design!

```html
<!DOCTYPE html>
<html lang="en">
<head>
<meta charset="utf-8">
<title>Ridgeline Design + Build — Business Card</title>
<link rel="stylesheet" href="https://fonts.googleapis.com/css2?family=Montserrat:wght@400;500;700&family=Oswald:wght@500&display=swap">
<style>
  :root {
    --page-bg: #1e1e1e;
    --card-white: #ffffff;
    --brand-green: #7dc12a;
    --ink: #1a1a1a;
    --ink-soft: #2b2b2b;
    --mark-grey: #d4d4d4;
    --mark-tint: #e6f2d8;
    --back-top: #2c2c2c;
    --back-bottom: #1b1b1b;
  }
  * { margin: 0; padding: 0; box-sizing: border-box; }
  html, body {
    width: 1200px; height: 897px; overflow: hidden;
    background: var(--page-bg);
    font-family: "Montserrat", Arial, sans-serif;
  }
  .card {
    position: absolute; left: 303px; width: 594px; height: 338px;
    border-radius: 16px; overflow: hidden;
  }
  .card--front { top: 92px; background: var(--card-white); }
  .card--back {
    top: 470px;
    background: linear-gradient(180deg, var(--back-top), var(--back-bottom));
  }

  /* front */
  .wordmark {
    position: absolute; left: 31px; top: 70px;
    display: flex; align-items: center; gap: 8px;
  }
  .wordmark__square { width: 14px; height: 14px; background: var(--brand-green); }
  .wordmark__name {
    font-weight: 700; font-size: 21px; letter-spacing: 0.5px; color: var(--ink);
    line-height: 1;
  }
  .wordmark__sub {
    position: absolute; left: 53px; top: 96px;
    font-weight: 700; font-size: 9px; letter-spacing: 3px; color: var(--ink);
  }
  .name-tab {
    position: absolute; left: 0; top: 184px; width: 9px; height: 42px;
    background: var(--brand-green); border-radius: 0 3px 3px 0;
  }
  .person-name {
    position: absolute; left: 31px; top: 176px;
    font-family: "Oswald", "Arial Narrow", sans-serif; font-weight: 500;
    font-size: 31px; line-height: 1; color: var(--brand-green);
  }
  .person-title {
    position: absolute; left: 31px; top: 214px;
    font-size: 14px; color: var(--ink-soft); letter-spacing: 0.3px;
  }
  .contact-list {
    position: absolute; left: 31px; top: 241px; list-style: none;
    font-size: 13.5px; color: var(--ink-soft);
  }
  .contact-list li { display: flex; align-items: center; gap: 5px; height: 18px; }
  .contact-list svg { width: 13px; height: 13px; flex: none; }
  .web-bar {
    position: absolute; left: 0; bottom: 0; width: 329px; height: 24px;
    background: var(--brand-green);
    color: var(--card-white); font-weight: 500; font-size: 13.5px;
    letter-spacing: 1.5px; line-height: 24px; padding-left: 31px;
  }
  .corner-mark {
    position: absolute; left: 333px; top: 100px; width: 261px; height: 238px;
    background: linear-gradient(135deg, var(--mark-tint) 0%, var(--mark-grey) 60%);
    opacity: 0.55;
  }

  /* back */
  .back-pattern {
    position: absolute; inset: 0;
    background: radial-gradient(ellipse at 80% 20%, rgba(255,255,255,0.08), transparent 60%),
                radial-gradient(ellipse at 20% 85%, rgba(0,0,0,0.35), transparent 60%);
  }
  .back-mark {
    position: absolute; left: 0; right: 0; top: 156px;
    display: flex; justify-content: center; align-items: center; gap: 8px;
  }
  .back-mark__square { width: 14px; height: 14px; background: var(--brand-green); }
  .back-mark__name {
    font-weight: 700; font-size: 21px; letter-spacing: 0.5px; color: var(--card-white);
  }
</style>
</head>
<body>
  <section class="card card--front" aria-label="Business card front">
    <div class="wordmark">
      <span class="wordmark__square"></span>
      <span class="wordmark__name">RIDGELINE</span>
    </div>
    <div class="wordmark__sub">DESIGN + BUILD</div>

    <div class="name-tab"></div>
    <h1 class="person-name">MARCUS HALE</h1>
    <p class="person-title">OWNER</p>

    <ul class="contact-list">
      <li>
        <svg viewBox="0 0 24 24" aria-hidden="true"><path fill="#7dc12a" d="M6.6 10.8a15.1 15.1 0 0 0 6.6 6.6l2.2-2.2c.3-.3.7-.4 1-.2 1.1.4 2.3.6 3.6.6.6 0 1 .4 1 1V20c0 .6-.4 1-1 1A17 17 0 0 1 3 4c0-.6.4-1 1-1h3.5c.6 0 1 .4 1 1 0 1.3.2 2.5.6 3.6.1.3 0 .7-.2 1z"/></svg>
        (555) 014-2287
      </li>
      <li>
        <svg viewBox="0 0 24 24" aria-hidden="true"><path fill="#7dc12a" d="M2 8c3-3 17-3 20 0v3h-5V9H7v2H2zM5 12h14l2 8H3zm7 2a2.5 2.5 0 1 0 0 5 2.5 2.5 0 0 0 0-5z"/></svg>
        (555) 014-2287
      </li>
      <li>
        <svg viewBox="0 0 24 24" aria-hidden="true"><rect x="2.5" y="5" width="19" height="14" rx="1.5" fill="none" stroke="#7dc12a" stroke-width="2"/><path d="M3 6l9 7 9-7" fill="none" stroke="#7dc12a" stroke-width="2"/></svg>
        ridgelinebuild@mail.com
      </li>
    </ul>

    <div class="web-bar">www.ridgelinebuild.com</div>
    <div class="corner-mark" role="img" aria-label="Large faint brand symbol decoration"></div>
  </section>

  <section class="card card--back" aria-label="Business card back">
    <div class="back-pattern" role="img" aria-label="Embossed repeating brand symbol pattern"></div>
    <div class="back-mark">
      <span class="back-mark__square"></span>
      <span class="back-mark__name">RIDGELINE</span>
    </div>
  </section>
</body>
</html>
```